Medical Billing Company Needs a Business Card Design

We need a business card design for a Florida based medical billing company called 'Clinicians Keystone Solutions'. We specialize in providing revenue cycle management services to physician and therapist offices (we're basically their back-office processing partner for providing billing software, claims submissions, A/R follow-up and patient statements & collections. Our logo is red and blue-ish, so make sure that whatever other elements are used will match appropriately. Our current business card design has a too small font size. I'd like to project an image that shows we are modern & reliable. On a side note, I'm planning on using ZUB for printing these cards.

Target Market(s)

Office managers, physicians, therapists

Industry/Entity Type

Printing

Requirements
Must have
• Logo
Name of Employee
Phone
Fax
E-mail
Website

```html
<!DOCTYPE html>
<html lang="en">
<head>
<meta charset="utf-8">
<title>Clinicians Keystone Solutions – Business Card</title>
<link rel="stylesheet" href="https://fonts.googleapis.com/css2?family=Source+Sans+3:wght@400;600;700&display=swap">
<style>
  :root {
    --page: #ebebef;
    --paper: #ffffff;
    --ink: #2b2b33;
    --brand-blue: #3a2a7c;
    --brand-violet: #5a4596;
    --brand-red: #b0222e;
    --back-light: #5e4a9c;
    --back-dark: #1d0b66;
    --rule: #c9c9cf;
    --shadow: rgba(30, 20, 60, 0.18);
  }
  * { box-sizing: border-box; margin: 0; padding: 0; }
  html, body { width: 1200px; height: 987px; overflow: hidden; }
  body {
    background: var(--page);
    font-family: "Source Sans 3", "Myriad Pro", Arial, sans-serif;
    color: var(--ink);
    position: relative;
  }
  .card {
    position: absolute;
    top: 339px;
    width: 540px;
    height: 309px;
    border-radius: 28px;
    box-shadow: 0 14px 34px var(--shadow);
    overflow: hidden;
  }
  .card-front { left: 40px; background: var(--paper); }
  .card-back {
    left: 620px;
    background: linear-gradient(135deg, var(--back-light) 0%, var(--back-dark) 100%);
    color: #fff;
  }

  /* front */
  .brand-name {
    position: absolute;
    top: 34px; left: 0; right: 0;
    text-align: center;
    font-size: 30px;
    font-weight: 600;
    letter-spacing: 1.5px;
    text-transform: uppercase;
    color: var(--brand-blue);
  }
  .divider {
    position: absolute;
    top: 100px; left: 40px; right: 40px;
    height: 2px;
    background: linear-gradient(90deg, transparent, var(--rule) 15%, var(--rule) 85%, transparent);
  }
  .person {
    position: absolute;
    top: 116px; left: 0; right: 0;
    text-align: center;
    font-size: 27px;
    font-weight: 700;
    color: var(--brand-violet);
  }
  .person .title { font-weight: 400; color: var(--brand-red); }
  .address {
    position: absolute;
    top: 160px; left: 0; right: 0;
    text-align: center;
    font-size: 17px;
  }
  .contact-row {
    position: absolute;
    left: 0; right: 0;
    display: flex;
    justify-content: center;
    gap: 26px;
    font-size: 17px;
  }
  .contact-row.phones { top: 192px; }
  .contact-row.online { top: 240px; }
  .contact-item { display: flex; align-items: center; gap: 7px; }
  .contact-item svg { width: 16px; height: 16px; flex: none; }

  /* back */
  .back-name {
    position: absolute;
    top: 104px; left: 0; right: 0;
    text-align: center;
    font-size: 30px;
    font-weight: 600;
    letter-spacing: 1px;
  }
  .back-web {
    position: absolute;
    bottom: 58px; left: 0; right: 0;
    text-align: center;
    font-size: 18px;
    letter-spacing: 4px;
  }
</style>
</head>
<body>

<section class="card card-front" aria-label="Business card front">
  <div class="brand-name">Clinicians Keystone Solutions</div>
  <div class="divider"></div>
  <div class="person">Your Name, <span class="title">Title</span></div>
  <div class="address">Street Name, City Name, State Zip Code</div>

  <div class="contact-row phones">
    <span class="contact-item">
      <svg viewBox="0 0 16 16" aria-hidden="true"><circle cx="8" cy="8" r="8" fill="var(--brand-blue)"/><path d="M5 4.5c.6-.4 1.1-.2 1.4.4l.5 1c.2.4 0 .8-.3 1l-.4.3c.4.9 1.1 1.6 2 2l.3-.4c.3-.3.7-.4 1-.2l1 .5c.6.3.7.9.3 1.4-.6.8-1.6 1-2.5.5A7 7 0 0 1 4.5 7c-.4-.9-.3-1.9.5-2.5z" fill="#fff"/></svg>
      123-456-0789
    </span>
    <span class="contact-item">
      <svg viewBox="0 0 16 16" aria-hidden="true"><rect x="4" y="1" width="8" height="14" rx="1.5" fill="var(--brand-blue)"/><rect x="5.3" y="3" width="5.4" height="8" fill="#fff"/><circle cx="8" cy="13" r=".8" fill="#fff"/></svg>
      123-456-0789
    </span>
  </div>

  <div class="contact-row online">
    <span class="contact-item">
      <svg viewBox="0 0 16 16" aria-hidden="true"><rect x="1" y="3" width="14" height="10" rx="1.5" fill="var(--brand-blue)"/><path d="M2 4.5l6 4.5 6-4.5" fill="none" stroke="#fff" stroke-width="1.3"/></svg>
      info@clinicianskeystone.com
    </span>
    <span class="contact-item">
      <svg viewBox="0 0 16 16" aria-hidden="true"><circle cx="8" cy="8" r="7" fill="var(--brand-blue)"/><g fill="none" stroke="#fff" stroke-width="1"><ellipse cx="8" cy="8" rx="3" ry="6.5"/><path d="M1.5 8h13M2.5 5h11M2.5 11h11"/></g></svg>
      www.clinicianskeystone.com
    </span>
  </div>
</section>

<section class="card card-back" aria-label="Business card back">
  <div class="back-name">Clinicians Keystone Solutions</div>
  <div class="back-web">www.clinicianskeystone.com</div>
</section>

</body>
</html>
```